QUORVIN CAPABILITY STATEMENT “Shaping Lasting Links”

QUORVIN CAPABILITY STATEMENT
“Shaping Lasting Links”
Indigenous-Owned Telecommunications & Infrastructure Solutions Partner

COVER PAGE

Visual: Modern and clean design featuring telecom towers, wind turbines, civil infrastructure, roads, and community WiFi imagery.
Tagline: “Linking Places, Lifting Futures.”
Contact:
Website: www.quorvin.com.au
Email: info@quorvin.com.au
Phone: [Insert Main Number]
“Proudly Indigenous-Owned | Compliant with Aboriginal Procurement Policy (APP) & SME Policies”
INTRODUCTION

Quorvin is a 100% Indigenous-owned leader in comprehensive infrastructure solutions, specializing in telecommunications, civil works, renewable energy, structural engineering, and site development. With over a decade of experience, we deliver safe, reliable, and culturally respectful services across Australia, from urban centers to remote wind farms and heritage sites. Our mission: “To bridge infrastructure gaps while empowering Indigenous communities and fostering sustainable growth.”

CORE CAPABILITIES

TELECOMMUNICATIONS

Tower Builds & Maintenance: Structural engineering, geotechnical analysis, foundation mapping.
Community WiFi Projects: Enhancing digital inclusion in Indigenous and remote communities.
Fiber & Wireless Networks: End-to-end installation for Velonet, Satellite, and regional connectivity.
Height Safety Systems: Design, inspection, and certification of lad-safe safety infrastructure.
CIVIL & STRUCTURAL ENGINEERING

Foundations & Concreting: Reinforced slabs, grillage, geotech-to-construction turnkey solutions.
Site Development: Earthworks, drainage, and access road/track construction.
Wind Farm Infrastructure: Reinforcing towers and integrating power systems for high-wind environments.
ROAD & ACCESS TRACK CONSTRUCTION

Construction of durable access roads and tracks: For remote projects and urban settings.
Remediation of existing tracks: Upgrading for environmental compliance and sustainability.
Facilitating logistics and site access: Particularly in challenging terrain.
POWER & ELECTRICAL SYSTEMS

Off-grid energy solutions: Solar hybrid systems, electrical structural engineering.
Grid upgrades: Ensuring compliance with AS/NZS standards and facilitating connection upgrades.
SITE REFURBISHMENT & DEMOLITION

Comprehensive refurbishment and demolition services: For outdated telecom sites and structures.
Environmentally responsible dismantling: Focused on recycling materials and minimizing land impact.
EMERGENCY RESPONSE SERVICES

24/7 Rapid Response: Over 450 callouts annually; 4,000+ emergencies resolved nationwide.
Disaster Recovery: Comprehensive support during floods, bushfires for Velonet, Marvaske, Trilumen, and regional clients.
PROJECT EXPERIENCE

Heritage Tower Upgrade

Enhanced safety and technology on culturally significant heritage sites, preserving their integrity.
Wind Farm Deployment

Delivered power, fiber, and reinforced foundations for large-scale renewable energy projects in high-wind environments.
Regional Fibre Network

Laid 200km of fiber in flood-prone regions, ensuring critical infrastructure resilience.
Indigenous Community WiFi & Connectivity

Installed sustainable WiFi networks to bridge the digital divide, supporting education, health, and business activities.
Site Demolition & Refurbishment

Safely decommissioned aging telecom sites and structures across Australia, emphasizing land reuse and environmental care.
Access Track Construction & Remediation

Developed new access roads and refurbished existing tracks to facilitate project logistics, particularly in remote or environmentally sensitive areas.
Key Stats:
+600 sites supported | 10-year Velonet partner | 98% client retention | Over 20 Indigenous community WiFi deployments

COMMITMENT TO SAFETY & QUALITY

“Pause Twice, Work Wise” Protocol: Enforced pre-task risk assessments to ensure safety at every stage.
Certifications: ISO 45001 (Safety) | ISO 9001 (Quality Management).
Safety Culture: Regular safety audits, Indigenous-led training programs, and safety initiatives focused on community well-being.
INDIGENOUS INCLUSION & COMMUNITY IMPACT

Elders Guidance Council: Provides guidance on community engagement, cultural sensitivity, and social responsibility.
Supplier Diversity: 30% procurement from Indigenous-owned businesses, fostering economic growth.
Regional Employment: 65% of our workforce originates from local communities, creating sustainable jobs.
Testimonial: “Quorvin’s partnership empowered our community with jobs and infrastructure that respects our land.” – Local Indigenous Leader

CONTACT & SERVICE AREAS

Headquarters: [Insert Address] | ABN: [Insert ABN]

24/7 Emergency Support: [Insert Dedicated Emergency Line]

Certifications & Registrations:

Trade Circle Registered, First Enterprise Register (FER)
SERVICE AREAS

National Coverage with Regional Expertise:
Major Cities: Sydney, Melbourne, Brisbane, Perth, Adelaide, Darwin, Hobart.
Regional & Remote Areas: Pilbara, Kimberley, Far North Queensland, Outback NSW.
Disaster Zones: Rapid response teams deployed nationwide for bushfire and flood incidents.
EMERGENCY SUPPORT

SLA Guarantee: 90% of emergencies addressed within 4 hours.
Partners Supported: Velonet, Marvaske, Trilumen, regional councils.
This capability statement reflects our commitment to quality, safety, and community engagement across all levels of operation, ensuring that we empower the communities we serve while maintaining the highest standards of service delivery.

Target Market(s)

Government Agencies: Especially those seeking to comply with Indigenous Procurement Policies. Telecommunication Operators: Such as Velonet, Marvaske, and Trilumen for infrastructure deployment. Indigenous Communities: Projects aimed at enhancing connectivity and digital inclusion. Utilities and Energy Providers: For power and electrical infrastructure projects. Construction and Engineering Firms: Seeking collaboration on civil and structural infrastructure projects.

Industry/Entity Type

Telecommunications and Infrastructure Development: Focused on service delivery in various contexts, including urban settings, remote locations, and Indigenous community projects. Renewable Energy: This includes wind and solar infrastructure linked to telecommunications enhancements. Civil Engineering: Related to building and maintaining essential infrastructure such as access roads and utility lines.

Font styles to use
Other font styles liked:
• Bubbleboddy neue

Requirements
Must have
• Clear demonstration of Indigenous ownership and community engagement. Compliance with relevant safety and quality certifications (e.g., ISO 45001, ISO 9001). Showcase of core capabilities in telecommunications, civil engineering, and those specific to renewable energy. Visuals that reflect the diverse range of services offered (like telecom towers and community WiFi installations).
Nice to have
• Interactive elements such as hyperlinks to project case studies or client testimonials. Infographics or visual data to highlight key statistics and project success rates. Cultural motifs or imagery that reflect Indigenous heritage and inclusion in design aspirations. QR codes that link to videos or more detailed project descriptions for digital formats.
Should not have
• Clutter or excessive text that detracts from the main messages. Generic stock images that don’t align with the specific projects or Indigenous culture. Technical jargon that could confuse stakeholders unfamiliar with industry-specific terms. Overemphasis on competitors; the focus should remain on Quorvin's unique strengths and contributions.

```html
<!DOCTYPE html>
<html lang="en">
<head>
<meta charset="utf-8">
<title>Quorvin Capability Statement – Contact &amp; Service Areas</title>
<link href="https://fonts.googleapis.com/css2?family=Montserrat:wght@300;400;500;600;700;800&display=swap" rel="stylesheet">
<style>
  :root {
    --red: #e8262a;
    --badge: #dc1f3c;
    --ink: #111111;
    --text: #2b2b2b;
    --paper: #ffffff;
    --backdrop: #dcdcdc;
    --map: #8a9fb0;
    --rule: #e8a0a2;
  }
  * { margin: 0; padding: 0; box-sizing: border-box; }
  html, body { width: 1200px; height: 842px; overflow: hidden; background: var(--backdrop); }
  body { font-family: "Montserrat", sans-serif; color: var(--text); position: relative; }
  .spread { position: absolute; left: 43px; top: 60px; width: 1114px; height: 721px; background: var(--paper); overflow: hidden; }
  .abs { position: absolute; }

  /* Contact block */
  .corner { position: absolute; border-color: var(--red); border-style: solid; }
  .corner--tr { left: 445px; top: 42px; width: 70px; height: 48px; border-width: 6px 6px 0 0; }
  .corner--bl { left: 42px; top: 197px; width: 74px; height: 49px; border-width: 0 0 6px 6px; }
  .contact-photo { left: 49px; top: 48px; width: 459px; height: 192px;
    background: linear-gradient(90deg, #6f7678 0%, #8a8f90 35%, #d9d7d3 62%, #c9a68c 78%, #e7e6e4 100%); }
  .contact-text { left: 88px; top: 90px; color: #fff; font-size: 11px; font-weight: 500; line-height: 12px; }
  .contact-text h2 { font-size: 16.5px; font-weight: 700; line-height: 20px; margin-bottom: 2px; }
  .contact-text .abn { margin-top: 14px; }
  .contact-text .support { margin-top: 2px; }

  /* Section headings */
  .heading { position: absolute; padding-left: 13px; font-size: 15px; line-height: 1.1; color: var(--ink); font-weight: 400; }
  .heading::before { content: ""; position: absolute; left: 0; top: 0; bottom: 0; width: 4px; background: var(--red); }
  .heading strong { display: block; font-weight: 700; }
  .heading--dark::before { background: var(--ink); }

  .badge { top: 271px; width: 77px; height: 98px; border-radius: 9px; background: var(--badge); }

  .label-red { top: 516px; font-size: 10.5px; font-weight: 600; color: var(--red); }

  .map { top: 486px; height: 164px; background: linear-gradient(160deg, #9db0bf, var(--map)); border-radius: 40% 45% 38% 42%; }
  .place { font-size: 7.5px; font-weight: 600; color: var(--ink); line-height: 9px; }
  .dot { width: 3px; height: 3px; border-radius: 50%; background: var(--red); }

  /* Footer */
  .footer-brand { top: 674px; font-size: 9.5px; font-weight: 600; color: var(--red); letter-spacing: .3px; }
  .footer-rule { top: 679px; height: 1px; background: var(--rule); }
  .footer-rule::before { content: ""; position: absolute; left: 0; top: -1px; width: 34px; height: 2px; background: var(--ink); }
  .page-no { top: 673px; width: 14px; height: 14px; background: var(--red); color: #fff; font-size: 8.5px; font-weight: 700; text-align: center; line-height: 14px; }

  /* Disaster panel */
  .disaster { left: 557px; top: 42px; width: 557px; height: 356px; background: var(--red); }
  .photo { top: 66px; height: 247px; }
  .photo--fire { left: 598px; width: 227px; background: linear-gradient(180deg, #b59c86 0%, #6c655d 40%, #3a3633 70%, #5a3a26 100%); }
  .photo--flood { left: 846px; width: 226px; background: linear-gradient(180deg, #a9aba5 0%, #7b6f56 30%, #9d7a4e 65%, #8c7355 100%); }
  .disaster-title { left: 598px; top: 322px; padding-left: 14px; color: #fff; font-size: 38px; font-weight: 300; line-height: 1; }
  .disaster-title::before { content: ""; position: absolute; left: 0; top: 6px; bottom: 2px; width: 4px; background: #fff; }
  .disaster-title strong { font-weight: 800; }
  .disaster-sub { left: 598px; top: 368px; color: #fff; font-size: 10.3px; font-weight: 400; line-height: 13px; white-space: nowrap; }

  /* Emergency */
  .emergency-facts { left: 598px; top: 481px; width: 230px; font-size: 10.5px; line-height: 12px; color: var(--ink); }
  .emergency-facts p { margin-bottom: 4px; }
  .emergency-facts .partners { line-height: 15.5px; }
  .emergency-facts strong { font-weight: 700; }
  .emergency-note { left: 598px; top: 551px; width: 232px; font-size: 10.3px; line-height: 12.8px; font-weight: 400; color: #333; }
  .photo--rope { left: 848px; top: 418px; width: 224px; height: 238px;
    background: linear-gradient(135deg, #b8bcbf 0%, #c43a32 30%, #6b6151 55%, #a8957a 80%, #c9ccce 100%); }
</style>
</head>
<body>
<main class="spread">
  <!-- Page 6 -->
  <div class="corner corner--tr"></div>
  <div class="corner corner--bl"></div>
  <div class="abs contact-photo" role="img" aria-label="Support operator wearing a headset in a bright office"></div>
  <div class="abs contact-text">
    <h2>CONTACT</h2>
    <p>Headquarters:<br>PO Box 2718 Kelvale,<br>NSW 2391</p>
    <p class="abn">ABN: 00044588</p>
    <p class="support">24/7 Emergency<br>Support:</p>
  </div>

  <h3 class="heading" style="left:45px; top:307px;">CERTIFICATIONS &amp;<strong>REGISTRATIONS:</strong></h3>
  <div class="abs badge" style="left:218px;" role="img" aria-label="Trade Circle certification badge"></div>
  <div class="abs badge" style="left:359px;" role="img" aria-label="Trade Circle certification badge"></div>

  <h3 class="heading" style="left:32px; top:418px; font-size:15.5px;">SERVICE<strong>AREAS</strong></h3>
  <div class="abs label-red" style="left:32px; top:456px;">Major Cities:</div>
  <div class="abs label-red" style="left:280px; top:456px;">Regional &amp; Remote Areas:</div>

  <div class="abs map" style="left:60px; width:172px;" role="img" aria-label="Map of Australia marking major cities"></div>
  <span class="abs place" style="left:149px; top:482px;">Darwin</span>
  <span class="abs place" style="left:237px; top:555px;">Brisbane</span>
  <span class="abs place" style="left:32px; top:575px;">Perth</span>
  <span class="abs place" style="left:240px; top:586px;">Sydney</span>
  <span class="abs place" style="left:126px; top:607px;">Adelaide</span>
  <span class="abs place" style="left:218px; top:615px;">Melbourne</span>
  <span class="abs dot" style="left:137px; top:494px;"></span>
  <span class="abs dot" style="left:230px; top:568px;"></span>
  <span class="abs dot" style="left:71px; top:584px;"></span>
  <span class="abs dot" style="left:219px; top:595px;"></span>
  <span class="abs dot" style="left:168px; top:602px;"></span>
  <span class="abs dot" style="left:195px; top:615px;"></span>

  <div class="abs map" style="left:299px; width:174px;" role="img" aria-label="Map of Australia marking regional and remote areas"></div>
  <span class="abs place" style="left:306px; top:482px;">Kimberley</span>
  <span class="abs place" style="left:435px; top:473px; text-align:center;">Far North<br>Queensland</span>
  <span class="abs place" style="left:297px; top:514px;">Pilbara</span>
  <span class="abs place" style="left:466px; top:520px; text-align:center;">Outback<br>NSW</span>
  <span class="abs dot" style="left:353px; top:510px;"></span>
  <span class="abs dot" style="left:428px; top:510px;"></span>
  <span class="abs dot" style="left:337px; top:543px;"></span>
  <span class="abs dot" style="left:428px; top:573px;"></span>

  <div class="abs footer-brand" style="left:43px;">QUORVIN</div>
  <div class="abs footer-rule" style="left:82px; width:420px;"></div>
  <div class="abs page-no" style="left:502px;">6</div>

  <!-- Page 7 -->
  <section class="abs disaster"></section>
  <div class="abs photo photo--fire" role="img" aria-label="Bushfire burning through eucalypt forest"></div>
  <div class="abs photo photo--flood" role="img" aria-label="Aerial view of a flooded regional town"></div>
  <h2 class="abs disaster-title">Disaster <strong>Zones</strong></h2>
  <p class="abs disaster-sub">Rapid response teams deployed nationwide for bushfire and flood incidents.</p>

  <h3 class="heading heading--dark" style="left:598px; top:433px; font-size:15.5px;">EMERGENCY<strong>SUPPORT</strong></h3>
  <div class="abs emergency-facts">
    <p><strong>SLA Guarantee:</strong> 90% of emergencies addressed within 4 hours.</p>
    <p class="partners"><strong>Partners Supported:</strong> Velonet, Marvaske, Trilumen, regional councils.</p>
  </div>
  <p class="abs emergency-note">This capability statement reflects our commitment to quality, safety, and community engagement across all levels of operation, ensuring that we empower the communities we serve while maintaining the highest standards of service delivery.</p>
  <div class="abs photo--rope" role="img" aria-label="Technician in a safety harness descending on ropes"></div>

  <div class="abs footer-brand" style="left:598px;">QUORVIN</div>
  <div class="abs footer-rule" style="left:637px; width:421px;"></div>
  <div class="abs page-no" style="left:1058px;">7</div>
</main>
</body>
</html>
```